Building technology company seek stationery design and folder design

Letterhead, and a folder design
ideally, I would have two letter head design, one is for one-page bussiness letter. the other one I can use for longer document such report, or analysis regular report page
you can find company logo and overall style at our website:
www.structavolt.example

we are in building technology business, using internet of things technology to improve building energy efficiency to make building greener.

Industry/Entity Type

It Company

Requirements
Must have
• company logo
Nice to have
• techy look abstract graphics, etc.
Should not have
• no comment

```html
<!DOCTYPE html>
<html lang="en">
<head>
<meta charset="utf-8">
<title>Structavolt Stationery</title>
<link href="https://fonts.googleapis.com/css2?family=Questrial&display=swap" rel="stylesheet">
<style>
  :root {
    --stage: #e4e4e4;
    --paper: #ffffff;
    --paper-shade: #ececec;
    --brand-green: #8dc63f;
    --folder-olive: #7f8070;
    --folder-line: #8c8e7c;
    --footer-band: #7a7a6a;
    --ink: #3a3a3a;
    --ink-soft: #555555;
    --white: #ffffff;
  }
  html, body {
    margin: 0;
    padding: 0;
    width: 1200px;
    height: 821px;
    overflow: hidden;
    background: var(--stage);
    font-family: "Questrial", sans-serif;
  }
  .canvas {
    position: relative;
    width: 1200px;
    height: 821px;
  }

  /* Letterhead */
  .letterhead {
    position: absolute;
    left: 75px;
    top: 114px;
    width: 440px;
    height: 620px;
    background: var(--paper);
    overflow: hidden;
  }
  .letterhead-backdrop {
    position: absolute;
    inset: 0;
    background: linear-gradient(90deg, var(--paper-shade) 0%, var(--paper) 35%, var(--paper) 60%, var(--paper-shade) 100%);
  }
  .letterhead-brand {
    position: absolute;
    left: 0;
    right: 0;
    top: 56px;
    display: flex;
    justify-content: center;
    align-items: center;
    gap: 7px;
  }
  .brand-square {
    width: 16px;
    height: 16px;
    background: var(--brand-green);
  }
  .brand-name {
    color: var(--brand-green);
    font-size: 15px;
    letter-spacing: 1.5px;
  }
  .letter-body {
    position: absolute;
    left: 39px;
    top: 172px;
    width: 364px;
    color: var(--ink-soft);
  }
  .salutation {
    margin: 0 0 18px;
    font-size: 11px;
    color: var(--ink);
  }
  .letter-body p.para {
    margin: 0 0 9px;
    font-size: 6px;
    line-height: 9.5px;
    text-align: justify;
  }
  .closing {
    margin: 14px 0 6px;
    font-size: 6px;
  }
  .signature {
    display: block;
    width: 80px;
    height: 28px;
    background: linear-gradient(90deg, rgba(141,198,63,0.35), rgba(141,198,63,0.1));
    border-radius: 3px;
  }
  .letterhead-footer-rule {
    position: absolute;
    left: 0;
    right: 0;
    top: 601px;
    height: 2px;
    background: var(--brand-green);
  }
  .letterhead-footer-mark {
    position: absolute;
    left: 375px;
    top: 590px;
    width: 10px;
    height: 10px;
    background: var(--brand-green);
  }
  .letterhead-footer {
    position: absolute;
    left: 0;
    right: 0;
    top: 603px;
    height: 17px;
    background: var(--footer-band);
    color: var(--white);
    font-size: 6.3px;
    display: flex;
    justify-content: center;
    align-items: center;
    gap: 6px;
  }
  .contact-item {
    display: inline-flex;
    align-items: center;
    gap: 2px;
  }
  .contact-item svg { width: 6px; height: 6px; }

  /* Folder */
  .folder {
    position: absolute;
    left: 553px;
    top: 77px;
    width: 520px;
    height: 659px;
    background: var(--folder-olive);
    overflow: hidden;
  }
  .folder-spine {
    position: absolute;
    top: 0;
    bottom: 0;
    width: 1px;
    background: var(--folder-line);
  }
  .folder-brand {
    position: absolute;
    left: 0;
    right: 0;
    top: 360px;
    display: flex;
    justify-content: center;
    align-items: center;
    gap: 12px;
  }
  .folder-brand .brand-square {
    width: 34px;
    height: 34px;
  }
  .folder-brand .brand-name {
    font-size: 34px;
    letter-spacing: 3px;
  }
</style>
</head>
<body>
<main class="canvas">

  <section class="letterhead" aria-label="Letterhead">
    <div class="letterhead-backdrop" role="img" aria-label="Soft grey network-of-nodes background pattern"></div>

    <header class="letterhead-brand">
      <span class="brand-square"></span>
      <span class="brand-name">STRUCTAVOLT</span>
    </header>

    <article class="letter-body">
      <p class="salutation">Dear Mr. Harlan,</p>
      <p class="para">Lorem ipsum dolor sit amet, consectetur adipiscing elit. Donec orci purus, luctus vitae dignissim eu, iaculis sed purus. Vivamus faucibus, ipsum nec aliquet viverra, leo mauris condimentum ligula, sit amet sagittis enim ligula quis arcu. Nam egestas tortor id nisi porttitor mattis. In tortor ante, ultricies in suscipit a, tempus non massa. Vivamus et auctor mi. Fusce vel massa nulla. Phasellus nec eros mauris, et scelerisque orci.</p>
      <p class="para">Donec malesuada orci vitae nulla accumsan porta a id massa. Quisque accumsan iaculis magna sit amet fringilla. Maecenas consequat, magna eget tincidunt semper, odio nibh rutrum mi, id feugiat ante nisi eu risus. Vestibulum nunc orci, rhoncus a placerat in, ultricies in mi. Cras mattis varius eros, vel fringilla nisi suscipit eget. Quisque scelerisque sagittis nulla at porttitor.</p>
      <p class="para">Sed id augue vitae urna euismod commodo aliquet a quam. Pellentesque arcu velit, cursus et malesuada ut, consequat et diam. Nullam erat sem, rhoncus id ullamcorper vitae, rhoncus et arcu. In ultricies ultricies nulla, ut rutrum nisi iaculis at. Donec eu magna a metus ornare faucibus. Fusce aliquet faucibus ultricies. Morbi semper, est id tincidunt gravida, sem arcu adipiscing lacus, ac bibendum nulla leo eu purus. Quisque nec diam sed risus consectetur a accumsan quis quis nibh. Vestibulum id purus lorem.</p>
      <p class="para">It is a long established fact that a reader will be distracted by the readable content of a page when looking at its layout. The point of using Lorem Ipsum is that it has a more-or-less normal distribution of letters, as opposed to using 'Content here, content here', making it look like readable English. Many desktop publishing packages</p>
      <p class="closing">Sincerely,</p>
      <span class="signature" role="img" aria-label="Handwritten signature of Jon Harlan in green"></span>
    </article>

    <span class="letterhead-footer-mark"></span>
    <div class="letterhead-footer-rule"></div>
    <footer class="letterhead-footer">
      <span class="contact-item">
        <svg viewBox="0 0 10 10" aria-hidden="true"><path d="M2 1 L4 1 L4.6 3.2 L3.4 4.2 Q4.6 6 5.8 6.6 L6.8 5.4 L9 6 L9 8 Q5 9 1.5 4.5 Q1 3 2 1Z" fill="currentColor"/></svg>
        (555) 010-2846
      </span>
      <span class="contact-item">
        <svg viewBox="0 0 10 10" aria-hidden="true"><rect x="0.5" y="2" width="9" height="6" fill="currentColor"/></svg>
        info@structavolt.example
      </span>
      <span class="contact-item">
        <svg viewBox="0 0 10 10" aria-hidden="true"><circle cx="5" cy="5" r="4.5" fill="currentColor"/></svg>
        www.structavolt.example
      </span>
      <span class="contact-item">structavolt</span>
    </footer>
  </section>

  <section class="folder" aria-label="Presentation folder cover">
    <div class="folder-spine" style="left:5px"></div>
    <div class="folder-spine" style="left:12px"></div>
    <div class="folder-spine" style="left:17px"></div>
    <div class="folder-brand">
      <span class="brand-square"></span>
      <span class="brand-name">STRUCTAVOLT</span>
    </div>
  </section>

</main>
</body>
</html>
```